Covid 19 Exit Strategy one page brochure

I would like to design, and will need URGENT help, a brochure detailing a Covid 19 Exit Strategy plan. This brochure will need to be understood easily and the graphics inside should make it easy for people to understand without reading the entire text. This project is quite urgent and needs to be completed THIS WEEK - by Saturday may 16th at the latest. I am attaching two examples. I will provide the text.

```html
<!DOCTYPE html>
<html lang="en">
<head>
<meta charset="utf-8">
<title>COVID-19 Phased Social &amp; Economical Restart</title>
<link rel="stylesheet" href="https://fonts.googleapis.com/css2?family=Poppins:wght@300;400;500;600;700;800&display=swap">
<style>
:root{
  --cyan:#00b0d2;
  --red:#c8203a;
  --ink:#1d1d1d;
  --white:#ffffff;
  --paper:#ffffff;
}
*{box-sizing:border-box;margin:0;padding:0}
html,body{width:1200px;height:2970px;overflow:hidden}
body{font-family:"Poppins",sans-serif;color:var(--ink);background:var(--paper);font-size:12.5px;line-height:1.24}
.section{position:relative;width:1200px;overflow:hidden}
.intro{height:880px;background:var(--paper);padding:70px 34px 0 34px}
.title{font-weight:300;font-size:62px;line-height:1;letter-spacing:-1px}
.subtitle{font-weight:300;font-size:29px;margin-top:6px}
.tagline{font-weight:300;font-size:30px;color:var(--cyan);margin-top:6px}
.byline{width:540px;background:var(--cyan);color:var(--white);text-align:center;margin-top:12px;padding:8px 10px 10px}
.byline .name{font-size:29px;font-weight:300;line-height:1.1}
.byline .name b{font-weight:700}
.byline .role{font-size:13px;font-weight:600}
.byline .role span{font-weight:300;border-left:1px solid var(--white);padding-left:8px;margin-left:8px}
.lead{width:540px;margin-top:22px;font-size:12.3px}
.photo{position:absolute;right:30px;top:160px;width:540px;height:500px;border-radius:48% 52% 44% 56%/50% 40% 60% 50%;background:radial-gradient(circle at 55% 40%,#f3f1ee 0%,#d9dde0 55%,#b7c3cb 100%)}
.section-heading{margin-top:44px;font-size:20px;font-weight:800;letter-spacing:-.3px}
.section-heading::before{content:"";display:block;width:64px;height:4px;background:var(--red);margin-bottom:12px}
.req-grid{display:grid;grid-template-columns:270px 430px 270px;column-gap:30px;margin-top:18px}
.item{display:flex;gap:12px;align-items:flex-start;margin-bottom:18px;text-align:justify}
.item p{flex:1}
.icon{flex:0 0 42px;width:42px;height:42px}
.blue{height:820px;background:var(--cyan);color:var(--white);padding:22px 30px 0}
.blue .item,.red .item{color:var(--white)}
.blue .cols3 .item{margin-bottom:26px}
.plan-title{text-align:center;font-size:21px;font-weight:700;letter-spacing:13px;margin-bottom:18px}
.stage-banner{display:flex;align-items:center;margin:0 auto 40px;background:var(--white);width:745px;height:60px;position:relative}
.stage-banner .label{flex:0 0 175px;white-space:nowrap;text-align:center;font-size:30px;font-weight:700;color:var(--cyan);border-right:1px solid #333;line-height:1.3}
.stage-banner::before{content:"";position:absolute;left:0;top:22px;border:8px solid transparent;border-left-color:var(--cyan)}
.stage-banner .text{flex:1;padding:0 10px;font-size:11.8px;color:var(--ink);line-height:1.2}
.stage-banner .text b{font-weight:600}
.cols3{display:grid;grid-template-columns:270px 360px 360px;column-gap:36px}
.cols2{display:grid;grid-template-columns:500px 500px;column-gap:60px;margin-top:30px}
.stage2{height:720px;background:var(--paper);padding:30px 30px 0}
.stage2 .stage-banner{background:var(--red);width:745px}
.stage2 .stage-banner .label{color:var(--white);border-right-color:var(--white)}
.stage2 .stage-banner .text{color:var(--white)}
.stage2 .stage-banner::before{border-left-color:var(--white)}
.stage2 .cols3{grid-template-columns:265px 260px 425px;column-gap:34px}
.red{height:550px;background:var(--red);padding:18px 30px 0}
.red .stage-banner{width:900px;height:74px;margin-bottom:26px}
.red .stage-banner .label{color:var(--red)}
.red .stage-banner::before{border-left-color:var(--red);top:29px}
.red .cols3{grid-template-columns:350px 350px 290px;column-gap:28px}
.red .item{margin-bottom:16px}
</style>
</head>
<body>
<svg width="0" height="0" style="position:absolute">
  <defs>
    <symbol id="ic" viewBox="0 0 42 42">
      <circle cx="21" cy="21" r="19" fill="#ffffff" stroke="#d8323f" stroke-width="2"/>
      <rect x="13" y="13" width="16" height="16" rx="3" fill="#f0b63a" stroke="#2a2a2a" stroke-width="1.2"/>
      <path d="M16 21h10M21 16v10" fill="none" stroke="#2a2a2a" stroke-width="1.6"/>
    </symbol>
    <symbol id="ic-person" viewBox="0 0 42 42">
      <circle cx="21" cy="21" r="19" fill="#ffffff" stroke="#d8323f" stroke-width="2"/>
      <circle cx="21" cy="16" r="5" fill="#f0b63a" stroke="#2a2a2a" stroke-width="1.2"/>
      <path d="M12 31c1-6 5-8 9-8s8 2 9 8" fill="#4aa3c8" stroke="#2a2a2a" stroke-width="1.4"/>
    </symbol>
    <symbol id="ic-pin" viewBox="0 0 42 42">
      <circle cx="21" cy="21" r="19" fill="#ffffff" stroke="#d8323f" stroke-width="2"/>
      <path d="M21 31s-7-8-7-13a7 7 0 0 1 14 0c0 5-7 13-7 13z" fill="#e44b4b" stroke="#2a2a2a" stroke-width="1.2"/>
      <circle cx="21" cy="18" r="2.5" fill="#ffffff" stroke="#2a2a2a" stroke-width="1.2"/>
    </symbol>
    <symbol id="ic-house" viewBox="0 0 42 42">
      <circle cx="21" cy="21" r="19" fill="#ffffff" stroke="#d8323f" stroke-width="2"/>
      <path d="M12 21l9-8 9 8v9H12z" fill="#f0b63a" stroke="#2a2a2a" stroke-width="1.2"/>
      <path d="M19 30v-5h4v5" fill="#e44b4b" stroke="#2a2a2a" stroke-width="1.4"/>
    </symbol>
    <symbol id="ic-bag" viewBox="0 0 42 42">
      <circle cx="21" cy="21" r="19" fill="#ffffff" stroke="#d8323f" stroke-width="2"/>
      <rect x="12" y="16" width="18" height="13" rx="2" fill="#4aa3c8" stroke="#2a2a2a" stroke-width="1.2"/>
      <path d="M17 16v-3h8v3M12 22h18" fill="none" stroke="#2a2a2a" stroke-width="1.6"/>
    </symbol>
    <symbol id="ic-bus" viewBox="0 0 42 42">
      <circle cx="21" cy="21" r="19" fill="#ffffff" stroke="#d8323f" stroke-width="2"/>
      <rect x="13" y="12" width="16" height="16" rx="3" fill="#4aa3c8" stroke="#2a2a2a" stroke-width="1.2"/>
      <path d="M13 21h16M16 28v3M26 28v3" fill="none" stroke="#2a2a2a" stroke-width="1.6"/>
    </symbol>
    <symbol id="ic-mask" viewBox="0 0 42 42">
      <circle cx="21" cy="21" r="19" fill="#ffffff" stroke="#d8323f" stroke-width="2"/>
      <path d="M13 17c5-2 11-2 16 0v6c-4 5-12 5-16 0z" fill="#8fd3c3" stroke="#2a2a2a" stroke-width="1.2"/>
      <path d="M13 19l-4-1M29 19l4-1" fill="none" stroke="#2a2a2a" stroke-width="1.6"/>
    </symbol>
    <symbol id="ic-shop" viewBox="0 0 42 42">
      <circle cx="21" cy="21" r="19" fill="#ffffff" stroke="#d8323f" stroke-width="2"/>
      <rect x="12" y="17" width="18" height="13" fill="#f0b63a" stroke="#2a2a2a" stroke-width="1.2"/>
      <path d="M11 17l3-5h14l3 5z" fill="#e44b4b" stroke="#2a2a2a" stroke-width="1.2"/>
      <path d="M18 30v-6h6v6" fill="#4aa3c8" stroke="#2a2a2a" stroke-width="1.2"/>
    </symbol>
  </defs>
</svg>

<section class="section intro">
  <h1 class="title">COVID-19</h1>
  <p class="subtitle">Phased Social &amp; Economical Restart</p>
  <p class="tagline">A Global Benchmark of Best Practices</p>
  <div class="byline">
    <div class="name">BY- <b>LENA HARTWELL</b></div>
    <div class="role">Senior Vice President &amp; Chief Quality Officer<span>Northbridge Biologics</span></div>
  </div>
  <p class="lead">Pandemics have, historically, seen their end both medically - via herd immunity or immunizations. And while there are several clinical trials underway for potential Covid-19 vaccines, we are still a long way from deploying an effective vaccine and one that will stand the test of time as the virus changes. Covid-19 pandemic will be considered 'ended' when there are only occasional traces of localized cases that are quickly contained in specific locations. Today and in the absence of an effective vaccine(s) and for the re-opening of the economies and social activities to be successful, it is critical that the following basic conditions be in place before any lockdowns are lifted and before social activities resume:</p>
  <div class="photo" role="img" aria-label="Photograph of a medical team in white coats and surgical masks, led by a doctor putting on gloves"></div>

  <h2 class="section-heading">GENERAL REQUIREMENTS</h2>
  <div class="req-grid">
    <div>
      <div class="item"><svg class="icon"><use href="#ic"/></svg><p>Single digit downward trend of documented cases within the past 14- days.</p></div>
      <div class="item"><svg class="icon"><use href="#ic"/></svg><p>Ability to screen and test symptomatic individuals within 24 hours of identification. Increased and sufficient testing capacity, to test at least 50% of all population if necessary within a timeframe of 3 months.</p></div>
      <div class="item"><svg class="icon"><use href="#ic-person"/></svg><p>Ability to track and trace infected patients and contacts on a live basis and across the country and ability to react quickly to any unusual trends or outbreaks.</p></div>
    </div>
    <div>
      <div class="item" style="width:270px"><svg class="icon"><use href="#ic-house"/></svg><p>Hospitals and the health care system are capable of treating patients without operating on a crisis mode.</p></div>
      <div class="item" style="width:270px"><svg class="icon"><use href="#ic"/></svg><p>Ability to surge ICU capacity on a short notice - 24h.</p></div>
      <div class="item" style="margin-top:22px"><svg class="icon"><use href="#ic"/></svg><p>Plan in place to trigger targeted or full-scale containment in case of sudden outbreaks</p></div>
      <div class="item" style="margin-top:26px"><svg class="icon"><use href="#ic-mask"/></svg><p>Mandatory use of masks (at least surgical grade) for everyone in all public areas and at work. Mandatory use of N95, or equivalent, masks for all healthcare front workers and for all government agencies and authorities that are involved in overseeing the containment activities.</p></div>
    </div>
    <div style="padding-top:128px">
      <div class="item" style="margin-bottom:32px"><svg class="icon"><use href="#ic"/></svg><p>Mandatory daily checks of body temperature for everyone at the workplace or entering public areas.</p></div>
      <div class="item"><svg class="icon"><use href="#ic-bag"/></svg><p>Mandatory sanitation in all places - use of disinfection available on a large scale.</p></div>
    </div>
  </div>
</section>

<section class="section blue">
  <h2 class="plan-title">PHASED COVID-19 LOCKDOWN EXIT STRATEGY PLAN</h2>
  <div class="stage-banner">
    <div class="label">STAGE 1</div>
    <div class="text">To enter this stage, additional to the general requirements, the Effective Reproduction Number (Rt) must be less than 1 and the death rate at less than 3%.<br><b>The economy and social activities can resume in this sequence:</b></div>
  </div>
  <div class="cols3">
    <div>
      <div class="item"><svg class="icon"><use href="#ic-person"/></svg><p>Elderly (60+ years old) and vulnerable individuals should continue to self-isolate.</p></div>
      <div class="item"><svg class="icon"><use href="#ic-person"/></svg><p>No more than 5 people maximum gathering at a time in public areas and at work.</p></div>
      <div class="item"><svg class="icon"><use href="#ic-house"/></svg><p>Work from home should continue whenever and as much as possible.</p></div>
      <div class="item"><svg class="icon"><use href="#ic"/></svg><p>Social distancing should continue to be re-enforced in public areas, at work and in all areas reopened.</p></div>
      <div class="item"><svg class="icon"><use href="#ic-pin"/></svg><p>Non-essential travel should be minimized between cities and regions (and within cities and regions where covid-19 infections are still a risk)</p></div>
    </div>
    <div>
      <div class="item"><svg class="icon"><use href="#ic-house"/></svg><p>Large businesses (300 people and more, manufacturing, services, etc.) can reopen progressively. Common areas should remain closed (cafeteria, restaurant, gym, meeting rooms of no more than 5 people).</p></div>
      <div class="item"><svg class="icon"><use href="#ic-bag"/></svg><p>Small businesses (300 people and less) can reopen as well with the same conditions as large businesses.</p></div>
      <div class="item"><svg class="icon"><use href="#ic-shop"/></svg><p>Commercial shops can reopen. Shops should control the flow of people in their facilities not to exceed 30% at a time of standard capacity. Shops should provide disinfectant and temperature control at entry.</p></div>
      <div class="item"><svg class="icon"><use href="#ic-shop"/></svg><p>Pharmacies will continue to be open. However, they must make available disinfectant for use by clients and will continue to comply with social distancing. Pharmacies should limit the number of client/patient in their stores not to exceed 30% of the standard capacity.</p></div>
    </div>
    <div>
      <div class="item"><svg class="icon"><use href="#ic-bus"/></svg><p>Transportation (buses, taxis, airlines) will resume progressively. No air travels permitted in and out of Covid-19 known hotspots, locally or internationally. Entry to country should be limited and strictly controlled. All landing passengers and visitors regardless of the country of origin should be tested for Covid-19 at arrival. All passengers and visitors will undergo a temperature check at arrival. No more than 3 people at a time in a taxi/ride car including the driver. All passengers wearing masks. Buses should operate with no more than 30% customer's capacity per bus.</p></div>
      <div class="item" style="margin-top:40px"><svg class="icon"><use href="#ic"/></svg><p>Religious sites can reopen with a maximum capacity of 30% or less. Social distancing and wearing masks is mandatory. Religious sites should organize (volunteers can help) to check body temperature of everyone accessing the site and provide disinfectant at entry.</p></div>
    </div>
  </div>
  <div class="cols2">
    <div>
      <div class="item" style="margin-bottom:30px"><svg class="icon"><use href="#ic-house"/></svg><p>Hotels &amp; tourism (museums, etc.) can reopen but must operate at 30% or less capacity. All common areas (restaurants, gyms, swimming pools, conference rooms, etc.) should remain closed.</p></div>
      <div class="item"><svg class="icon"><use href="#ic-shop"/></svg><p>Coffee &amp; restaurants can reopen but must operate at 30% capacity as well and comply with social distancing. Clients must wear as much as possible their masks if they are not consuming food/coffee. Clients should avoid to talking to each other with masks off.</p></div>
    </div>
    <div>
      <div class="item" style="margin-bottom:30px"><svg class="icon"><use href="#ic-house"/></svg><p>All schools should remain closed. On-line courses should continue be the preferred method for education</p></div>
      <div class="item"><svg class="icon"><use href="#ic"/></svg><p>Large scale events (cinema, theaters, sport, business conferences, etc.) should remain closed or operate virtually. Sport events can resume but without spectators. Athletes and the staff surrounding them should be tested, disinfectants should be available and masks used as much as reasonably possible.</p></div>
    </div>
  </div>
</section>

<section class="section stage2">
  <div class="stage-banner">
    <div class="label">STAGE 2</div>
    <div class="text">To enter this stage, additional to the general requirements, the Effective Reproduction Number (Rt) must be less than 1 and the death rate at less than 3%.<br><b>The economy and social activities can resume in this sequence:</b></div>
  </div>
  <div class="cols3">
    <div>
      <div class="item" style="margin-bottom:70px"><svg class="icon"><use href="#ic-person"/></svg><p>Elderly (60+ years old) and vulnerable individuals should continue to self-isolate as much as possible.</p></div>
      <div class="item" style="margin-bottom:70px"><svg class="icon"><use href="#ic-person"/></svg><p>No more than 10 people maximum gathering at a time in public areas and at work.</p></div>
      <div class="item" style="margin-bottom:56px"><svg class="icon"><use href="#ic-house"/></svg><p>Work from home should if possible or for jobs that do not have to be necessarily in an office setup.</p></div>
      <div class="item" style="margin-bottom:46px"><svg class="icon"><use href="#ic-mask"/></svg><p>Social distancing can be relaxed. However people should continue to wear masks and use disinfectants</p></div>
      <div class="item"><svg class="icon"><use href="#ic-pin"/></svg><p>Travel can resume between cities and regions. The same containment restrictions should apply to any existing hotspot.</p></div>
    </div>
    <div>
      <div class="item" style="margin-bottom:60px"><svg class="icon"><use href="#ic-person"/></svg><p>Elective surgeries can resume in hospitals and clinics that are equipped to comply with all general requirements.</p></div>
      <div class="item" style="margin-bottom:30px"><svg class="icon"><use href="#ic-house"/></svg><p>Large businesses (300 people and more, manufacturing, services, etc.) will continue to operate. Common areas should open but social distancing should remain (cafeteria, restaurant, gym, meeting rooms of no more than 10 people).</p></div>
      <div class="item" style="margin-bottom:34px"><svg class="icon"><use href="#ic-bag"/></svg><p>Small businesses (300 people and less) will continue to operate with the same conditions as large businesses.</p></div>
      <div class="item" style="margin-bottom:34px"><svg class="icon"><use href="#ic-shop"/></svg><p>Commercial shops will continue to be open and can operate at 50% capacity. Wear of masks should continue.</p></div>
      <div class="item"><svg class="icon"><use href="#ic-shop"/></svg><p>Pharmacies will continue to be open and will need to operate a 50% capacity</p></div>
    </div>
    <div>
      <div class="item"><svg class="icon"><use href="#ic-bus"/></svg><p>Transportation (buses, taxis, and airlines) will continue to operate. Still no air travels permitted in and out of Covid-19 known hotspots, locally or internationally. Entry to country should be relaxed but remain controlled. Airports should continue to use thermo cameras to monitor passenger's temperature at landing. Airports should be equipped to test for Covid-19 if necessary. Transportation by taxi/ride car continues, however, passengers wear masks. Buses could operate with 50% capacity per bus.</p></div>
      <div class="item"><svg class="icon"><use href="#ic"/></svg><p>Religious sites can operate with a maximum capacity of 50%. Social distancing and wearing masks should be enforced. Sites should continue to check body temperature of everyone accessing the site and provide disinfectant at entry.</p></div>
      <div class="item"><svg class="icon"><use href="#ic-house"/></svg><p>Hotels &amp; tourism (museums, etc.) can operate at 50% capacity. All common areas (restaurants, gyms, swimming pools, conference rooms, etc.) could reopen. Gatherings are limited to 10 people or less and can be expanded with social distancing and wearing protective masks.</p></div>
      <div class="item"><svg class="icon"><use href="#ic-shop"/></svg><p>Coffee &amp; restaurants can operate at 50% capacity and continue comply with social distancing. Clients must wear as much as possible their masks if they are not consuming food/coffee.</p></div>
      <div class="item"><svg class="icon"><use href="#ic-house"/></svg><p>Schools can reopen in parallel with on-line education. Social distancing and re-arranging school seating to prevent the spread of infection is mandatory</p></div>
      <div class="item"><svg class="icon"><use href="#ic"/></svg><p>Large scale events (cinema, theaters, sport, business conferences, etc.) could resume under strict social distancing. People should wear masks.</p></div>
    </div>
  </div>
</section>

<section class="section red">
  <div class="stage-banner">
    <div class="label">STAGE 3</div>
    <div class="text">To enter stage 3 of the Covid-19 Exit Strategy, compliance to the general requirements is compulsory, additional to a successful Stage 2 outcome. The Effective Reproduction Number (Rt) for Stage 3 must be less than 0.3 and the death rate stabilized at less than 1%.<br><b>The economy and social activities can resume in this sequence:</b></div>
  </div>
  <div class="cols3">
    <div>
      <div class="item"><svg class="icon"><use href="#ic-person"/></svg><p>Elderly (60+ years old) and vulnerable individuals may resume all previously exercised activities without restrictions. Restrictions as to the number of people gathering together can be lifted. Social distancing can be relaxed. However, wear of masks may continue.</p></div>
      <div class="item"><svg class="icon"><use href="#ic-bag"/></svg><p>Travel can resume between cities and regions and out of country travel. The same containment restrictions as Stage 1 and 2 would continue to apply to any existing hotspot</p></div>
      <div class="item"><svg class="icon"><use href="#ic"/></svg><p>All hospital and clinic surgeries can resume in hospitals in compliance with standard hospital and health care procedures.</p></div>
      <div class="item"><svg class="icon"><use href="#ic-house"/></svg><p>Large businesses (300 people and more, manufacturing, services, etc.) will resume normal business practices. Wear of masks is recommended but not mandatory.</p></div>
    </div>
    <div>
      <div class="item"><svg class="icon"><use href="#ic-bag"/></svg><p>Small businesses (300 people and less) will operate with the same conditions as large businesses.</p></div>
      <div class="item"><svg class="icon"><use href="#ic-shop"/></svg><p>Commercial shops can operate on a normal mode - previous to covid- 19. Wear of masks could be recommended in certain areas</p></div>
      <div class="item"><svg class="icon"><use href="#ic-shop"/></svg><p>Pharmacies can operate at a normal state.</p></div>
      <div class="item"><svg class="icon"><use href="#ic-bus"/></svg><p>Transportation (buses, taxis, and airlines) will operate at a normal capacity. Still no air travels permitted in and out of Covid-19 known hotspots, locally or internationally. Entry to country should be relaxed and operate normally. Airports should continue to use thermo cameras to monitor passenger's temperature at landing. Airports should be equipped to test for Covid-19 if necessary. Transportation by taxi/ride car and buses will resume on a normal mode. Wear of masks is elective.</p></div>
    </div>
    <div>
      <div class="item"><svg class="icon"><use href="#ic"/></svg><p>Religious sites can operate normally. Wear of masks should be elective</p></div>
      <div class="item"><svg class="icon"><use href="#ic-house"/></svg><p>Hotels &amp; tourism (museums, etc.) can operate at 100% capacity including all common areas</p></div>
      <div class="item"><svg class="icon"><use href="#ic-shop"/></svg><p>Coffee &amp; restaurants can resume normal operations. Clients may wear masks for personal protection if they wish to.</p></div>
      <div class="item"><svg class="icon"><use href="#ic-house"/></svg><p>Schools can resume operations. Re-arranging school seating should continue until a vaccine is found.</p></div>
      <div class="item"><svg class="icon"><use href="#ic-mask"/></svg><p>Large scale events (cinema, theaters, sport, business conferences, etc.) could resume under moderate social distancing. People may elect to wear masks.</p></div>
    </div>
  </div>
</section>
</body>
</html>
```